Business Card Design

We are a company that provides stump grinding services for residential and commercial clients. Looking for a simple business card design that may have some type of graphic on the card that will tie in with the Tamsen name(Grizzly Bear, Paw Print, etc) . Possibly some foliage wrapping around part of the card? Would like to have a simple design that stands out because it is unique. We are working on getting the website set up and there is a simple graphic on the top of the page that came to mind when I mentioned the leaves.

Industry/Entity Type

Business

Contact Information for Business Card

Tamsen Stump Grinding 303-257-4788KodiakStumps.Com

Font styles to use
Serif

Requirements
Must have
• Business name
• Website Address
• Phone Number
Nice to have
• Graphics that would be associated with a Tamsen bear.
Should not have
• Nothing frilly

```html
<!DOCTYPE html>
<html lang="en">
<head>
<meta charset="utf-8">
<title>Tamsen Stump Grinding – Business Card</title>
<link rel="stylesheet" href="https://fonts.googleapis.com/css2?family=Montserrat:wght@400;500&family=Open+Sans:wght@400&display=swap">
<style>
  :root {
    --canvas-bg: #eceef1;
    --card-black: #000000;
    --brand-blue: #3b9bf2;
    --blue-deep: #1683f6;
    --blue-light: #52a9ff;
    --grey-text: #8a8a8a;
    --white: #ffffff;
  }
  * { margin: 0; padding: 0; box-sizing: border-box; }
  html, body {
    width: 1200px;
    height: 900px;
    overflow: hidden;
    background: var(--canvas-bg);
  }
  .canvas {
    position: relative;
    width: 1200px;
    height: 900px;
  }
  .card {
    position: absolute;
    width: 556px;
    height: 342px;
    overflow: hidden;
    box-shadow: 0 6px 18px rgba(0, 0, 0, 0.18);
  }
  /* Front */
  .card-front {
    left: 238px;
    top: 62px;
    background: var(--card-black);
    text-align: center;
  }
  .brand-badge {
    position: absolute;
    left: 208px;
    top: 35px;
    width: 132px;
    height: 132px;
    border-radius: 50%;
    border: 4px solid var(--white);
    display: flex;
    align-items: center;
    justify-content: center;
    font-family: "Montserrat", sans-serif;
    font-weight: 500;
    font-size: 22px;
    color: var(--brand-blue);
  }
  .front-name {
    position: absolute;
    left: 0;
    width: 100%;
    padding-left: 0;
    font-family: "Montserrat", sans-serif;
    font-weight: 500;
    text-transform: uppercase;
  }
  .front-name .name-main {
    position: absolute;
    left: 0; width: 100%;
    top: 170px;
    font-size: 25px;
    color: var(--brand-blue);
    letter-spacing: 0.01em;
  }
  .front-name .name-sub {
    position: absolute;
    left: 0; width: 100%;
    top: 207px;
    font-size: 14px;
    font-weight: 400;
    color: var(--grey-text);
    letter-spacing: 0.85em;
    padding-left: 0.85em;
  }
  .contact {
    position: absolute;
    left: 0;
    width: 100%;
    top: 256px;
    font-family: "Open Sans", sans-serif;
    font-size: 16px;
    line-height: 24px;
  }
  .contact-phone { color: var(--white); }
  .contact-web { color: var(--brand-blue); }

  /* Back */
  .card-back {
    left: 458px;
    top: 518px;
    width: 560px;
    background: linear-gradient(90deg, var(--blue-deep) 0%, var(--blue-light) 100%);
  }
  .back-ring {
    position: absolute;
    left: 0; top: 0;
    width: 560px;
    height: 342px;
  }
  .back-name {
    position: absolute;
    left: 146px;
    top: 146px;
    font-family: "Montserrat", sans-serif;
    font-weight: 500;
    text-transform: uppercase;
    color: var(--white);
  }
  .back-name .name-main {
    display: block;
    font-size: 31px;
    letter-spacing: 0.01em;
    line-height: 40px;
  }
  .back-name .name-sub {
    display: block;
    font-size: 18px;
    font-weight: 400;
    letter-spacing: 0.95em;
    margin-top: 6px;
  }
</style>
</head>
<body>
<main class="canvas">
  <section class="card card-front" aria-label="Business card front">
    <div class="brand-badge">Tamsen</div>
    <h1 class="front-name">
      <span class="name-main">Tamsen Stump</span>
      <span class="name-sub">Grinding</span>
    </h1>
    <div class="contact">
      <p class="contact-phone">303-555-0146</p>
      <p class="contact-web">www.tamsenstumps.com</p>
    </div>
  </section>

  <section class="card card-back" aria-label="Business card back">
    <svg class="back-ring" viewBox="0 0 560 342" aria-hidden="true">
      <circle cx="303" cy="172" r="205" fill="none" stroke="#ffffff" stroke-opacity="0.14" stroke-width="16"/>
    </svg>
    <h2 class="back-name">
      <span class="name-main">Tamsen Stump</span>
      <span class="name-sub">Grinding</span>
    </h2>
  </section>
</main>
</body>
</html>
```